Business Card Design

We would like to re-design our business cards. Our Company - Qwinrel Turbochargers, rebuilds turbochargers and sells replacement parts. Our website is: http://www.qwinrelturbochargers-example.com
We just had our logo changed. I will attach the file. Looking for fresh new/modern business card. We like the colors red, black, white and silver. Black background looks attractive, but not a requirement. The final design should communicate reasonable/competitive prices, top quality and reliability of our products.
Updates
Project Deadline Extended
Reason: Need to finalize the info on the card. Currently working on changing address and email info. Want to make sure it is the correct one before accepting the final design. Unless, this is something that can be changed at a later time..??
Industry/Entity Type
Business
Contact Information for Business Card
QWINREL TURBOCHARGERS, LLC
20473 Harwick Lane NE
Brenford, NV 89731
Tel: +1-555-214-7390
Fax: +1-555-267-1842
info@QwinrelTurbochargers-example.com
Our current business card had the following highlights:
*We rebuild all Turbocharges for Automotive, Diesel and Industrial
*Precision Balancing and in-house turbocharger needs
*All Turbocharger replacement parts are made in USA / U.K.
Look and feel
Each slider illustrates characteristics of the customer's brand and the style your logo design should communicate.

```html
<!DOCTYPE html>
<html lang="en">
<head>
<meta charset="utf-8">
<title>Qwinrel Turbochargers – Business Card</title>
<link rel="stylesheet" href="https://fonts.googleapis.com/css2?family=Open+Sans:wght@400;600;700&display=swap">
<style>
  :root {
    --stage: #e4e2de;
    --card-black: #0b0b0c;
    --card-sheen: #2a2a2d;
    --brand-red: #e3232f;
    --deep-red: #a8141d;
    --text-white: #f2f2f2;
    --text-silver: #b9bcc1;
    --divider: #6a6c70;
  }
  * { box-sizing: border-box; margin: 0; padding: 0; }
  html, body { width: 1200px; height: 1023px; overflow: hidden; }
  body {
    background: var(--stage);
    font-family: "Open Sans", Arial, sans-serif;
    position: relative;
  }
  .card {
    position: absolute;
    left: 300px;
    width: 600px;
    height: 340px;
    border-radius: 22px;
    overflow: hidden;
    background: linear-gradient(160deg, var(--card-sheen) 0%, var(--card-black) 45%, var(--card-black) 100%);
    box-shadow: 0 10px 26px rgba(0,0,0,0.25);
    color: var(--text-white);
  }
  .card--front { top: 150px; }
  .card--back { top: 533px; }

  .brand {
    display: flex;
    align-items: center;
    gap: 12px;
    white-space: nowrap;
  }
  .brand__dot {
    width: 26px; height: 26px;
    border-radius: 50%;
    background: var(--brand-red);
    flex: none;
  }
  .brand__name {
    font-weight: 700;
    font-size: 26px;
    color: var(--text-white);
    letter-spacing: 0.3px;
  }

  /* front */
  .card--front .brand { position: absolute; left: 42px; top: 44px; }
  .holder {
    position: absolute; left: 42px; top: 150px;
    font-size: 14px; line-height: 1.45;
    white-space: nowrap;
  }
  .holder__name { color: var(--brand-red); font-weight: 700; font-size: 18px; }
  .holder__company { color: var(--brand-red); font-size: 13px; margin-top: 4px; }
  .holder__address { color: var(--text-white); }
  .divider {
    position: absolute; left: 268px; top: 130px;
    width: 1px; height: 120px;
    background: linear-gradient(var(--card-black), var(--divider), var(--card-black));
    transform: rotate(18deg);
  }
  .contacts {
    position: absolute; left: 296px; top: 150px;
    list-style: none;
    font-size: 12px; line-height: 1;
    white-space: nowrap;
  }
  .contacts li { display: flex; align-items: center; gap: 10px; margin-bottom: 13px; }
  .contacts svg { width: 14px; height: 14px; flex: none; }
  .red-edge {
    position: absolute; left: 0; right: 0; bottom: 0; height: 30px;
    background: linear-gradient(var(--brand-red), var(--deep-red));
  }

  /* back */
  .card--back .brand { position: absolute; right: 40px; top: 58px; }
  .card--back .brand__name { font-size: 32px; }
  .highlights {
    position: absolute; left: 40px; top: 150px; right: 30px;
    list-style: none;
    color: var(--brand-red);
    font-size: 14px; line-height: 1.55;
    white-space: nowrap;
  }
  .highlights .cont { padding-left: 12px; }
</style>
</head>
<body>

<section class="card card--front" aria-label="Business card front">
  <div class="brand">
    <span class="brand__dot"></span>
    <span class="brand__name">Qwinrel Turbochargers</span>
  </div>

  <div class="holder">
    <p class="holder__name">Daren Kolby</p>
    <p class="holder__company">QWINREL TURBOCHARGERS, LLC</p>
    <p class="holder__address">20473 Harwick Lane NE</p>
    <p class="holder__address">Brenford, NV 89731</p>
  </div>

  <span class="divider"></span>

  <ul class="contacts">
    <li>
      <svg viewBox="0 0 16 16"><path fill="#e3232f" d="M3.5 1h2.5l1.2 3.5-1.7 1.2a9 9 0 0 0 4.8 4.8l1.2-1.7L15 10v2.5c0 1.4-1.1 2.5-2.5 2.5C6.4 15 1 9.6 1 3.5 1 2.1 2.1 1 3.5 1z"/></svg>
      +1-555-214-7390
    </li>
    <li>
      <svg viewBox="0 0 16 16"><rect x="4" y="1" width="8" height="5" fill="#e3232f"/><rect x="1" y="6" width="14" height="6" rx="1" fill="#e3232f"/><rect x="4" y="10" width="8" height="5" fill="#fff"/></svg>
      +1-555-267-1842
    </li>
    <li>
      <svg viewBox="0 0 16 16"><rect x="1" y="3" width="14" height="10" rx="1" fill="#e3232f"/><path d="M1.5 3.5 8 9l6.5-5.5" stroke="#0b0b0c" stroke-width="1.3" fill="none"/></svg>
      info@QwinrelTurbochargers-example.com
    </li>
    <li>
      <svg viewBox="0 0 16 16"><circle cx="8" cy="8" r="7" fill="#e3232f"/><path d="M1 8h14M8 1c-3 3-3 11 0 14M8 1c3 3 3 11 0 14" stroke="#0b0b0c" stroke-width="1" fill="none"/></svg>
      www.qwinrelturbochargers-example.com
    </li>
  </ul>

  <div class="red-edge"></div>
</section>

<section class="card card--back" aria-label="Business card back">
  <div class="brand">
    <span class="brand__dot"></span>
    <span class="brand__name">Qwinrel Turbochargers</span>
  </div>

  <ul class="highlights">
    <li>* We rebuild all Turbocharges for Automotive, Diesel and Industrial</li>
    <li>* Precision Balancing and in-house turbocharger needs</li>
    <li>* Extensive line of OEM Turbochargers in Stock for</li>
    <li class="cont">Varnet, Kellhorn, Dunsel, TKR, ORB and more..</li>
    <li>* All Turbocharger replacement parts are made in USA / U.K.</li>
  </ul>
</section>

</body>
</html>
```